Web design for new streaming audio service

We need a homepage design for a new streaming audio service. Our company is called Dunmoral, and we’re basically Vexlo for Audiobooks, Stand-Up Comedy, Lectures, Language Learning, etc. Essentially like Plumtrek for everything audio EXCEPT music.
You don’t have to code the homepage (Design Only), but it should include 3 different designs to work with 1) Web; 2) Phones; 3) Tablets.
Below is a link to a mockup of the web version which gives a good idea of what elements we want. This is just a mockup and we want you to improve it.
Once you download the mockup, please refer to the more detailed instructions below:
The following outlines the design project for the Dunmoral homepage. We have provided a rough mockup of the homepage layout that gives you a general idea of what we’re going for. There are a few elements that we are attached to, and many others where you have complete creative freedom to do whatever you think looks good.
The ZIP file includes the following:
* Mockup to see what we have in mind (dunmoral-homepage-mockup.jpg)
* Text used (dunmoral-homepage-text.txt)
* Raw image of actor (dunmoral-actor1.jpg)
* Raw images for samples (dunmoral-sample-[name].jpg)
Although we have only provided a mockup layout for the web version, we also need you to provide a mobile phone and a tablet version of the design also. It’s very possible the tablet version may be substantially similar to the web version, but the mobile phone version will likely be much different.
All of the raw files are included in the attached ZIP file. Please use our photographs and text as provided although cropping, sizing, etc. is flexible per the instructions below.
Display Requirements:
* Web Version - Minimum resolution 1024x768 (72 dpi) but should look good on 1920x1080 (72 dpi) - Page should be designed to scale to look acceptable in all resolutions in between.
* Phone Version - Minimum Zarno 4 - 640x960 (326 dpi) but should look good on Harlow Quasar T5 - 1920x1080 (441 dpi) - Page should be designed to scale to look acceptable in all resolutions and devices in between.
* Tablet Version - Minimum Bristly Ember QX 7” - 1280x800 (216 dpi) but should also look good on a Tavo Breeze - 2048x1536 (264 dpi) - Page should be designed to scale to look acceptable in all resolutions and devices in between.
Above the Fold - We want to make sure the Dunmoral logo, Member Login Link, Large Photo, Headline, Price, Button, and the first row of sample images are all “Above the fold”. As a general guideline, this means 600 pixels high on a 1024x768 72 dpi web screen. This requirement is less important on Phone versions.
Top Logo Bar - We want to retain the blue bar with the Dunmoral logo on the page, although we are open to a different size, shape and positioning if it greatly enhances the design. Please use the standard logo color, although you are welcome to use either the horizontal or vertical orientation of the logo based on your design.
Text color, font and size - Feel free to design the text in anyway you choose as long as the text is readable on the target platforms.
Buttons - Feel free to use any size, shape and colors for the buttons as long as they are obvious and clickable relative to the page. The only exception is the Chatterly button should follow the Chatterly color scheme and logo treatment (the mockup doesn’t seem 100% correct.)
Top Photograph - We want to retain the large photograph across the top of the screen although final shape and dimensions are flexible.
Size and shape of content samples (i.e. Audiobooks, Stand-Up Comedy, etc.) - Feel free to design the content samples in anyway you choose.
Three Sales Points (i.e. Listen on your Zarno…, All you can enjoy…, etc.) - The Three Sales Points are envisioned to each have a corresponding illustration which you should provide and have rights for. The placeholder is represented by a square next to the text. The color size and shape of these elements are flexible and can be designed in any way you choose.
Opt-in form - Feel free to design the opt-in form in anyway you choose as long as the text is readable and the interactivity is obvious on the target platforms.
Text links and copyright notice - Feel free to design the bottom of the page text links and copyright notice in anyway you choose.
Additional colors, graphic design elements, etc. - Feel free to use any additional colors, graphic design elements, etc. to support your design.
people who want to listen to audio through their mobile devices.
Graphic Design

```html
<!DOCTYPE html>
<html lang="en">
<head>
<meta charset="utf-8">
<title>Dunmoral – Unlimited Listening</title>
<link href="https://fonts.googleapis.com/css2?family=Roboto:wght@400;700&display=swap" rel="stylesheet">
<style>
:root{
  --sky:#5aaad3;
  --sky-deep:#4f9dc6;
  --heading:#4a9fcc;
  --ink:#444;
  --band:#f0f0f0;
  --access:#3f89b5;
  --social:#5b6aa3;
  --social-dark:#4c5a90;
  --orange-top:#f8a04a;
  --orange-bot:#ee7a1c;
  --white:#fff;
}
*{box-sizing:border-box;margin:0;padding:0}
html,body{width:1080px;height:1200px;overflow:hidden;background:var(--white)}
body{position:relative;font-family:'Roboto',Arial,sans-serif;color:var(--ink)}
.abs{position:absolute}

.topbar{left:0;top:0;width:1080px;height:66px;background:var(--sky)}
.brand{left:155px;top:17px;display:flex;align-items:center;gap:8px;color:var(--white);font-size:24px;font-weight:400}
.brand-dot{width:22px;height:22px;border-radius:50%;background:var(--white)}
.member-login{left:822px;top:20px;width:104px;height:28px;border:1px solid var(--white);color:var(--white);font-size:9px;display:flex;align-items:center;justify-content:center}

.hero{left:0;top:66px;width:1080px;height:442px;background:var(--white)}
.hero-photo{left:170px;top:66px;width:910px;height:442px;
  background:linear-gradient(90deg,rgba(255,255,255,1) 0%,rgba(255,255,255,.9) 22%,rgba(214,170,140,.6) 48%,#c99576 62%,#a57560 78%,#6d7f9a 100%)}
.hero-fade{left:170px;top:430px;width:910px;height:78px;background:linear-gradient(180deg,rgba(90,110,140,0),rgba(80,100,135,.45))}
.headline{left:110px;top:184px;width:450px;text-align:center;color:var(--heading);font-weight:700;font-size:34px;letter-spacing:.5px}
.subline{left:110px;top:226px;width:450px;text-align:center;color:var(--heading);font-weight:700;font-size:26px}
.price{left:110px;top:267px;width:450px;text-align:center;font-size:18px;color:#333}
.cta-trial{left:206px;top:308px;width:257px;height:49px;border-radius:3px;background:linear-gradient(180deg,var(--orange-top),var(--orange-bot));color:var(--white);font-size:19px;display:flex;align-items:center;justify-content:center;box-shadow:0 1px 2px rgba(0,0,0,.2)}
.trial-note{left:110px;top:368px;width:450px;text-align:center;font-size:10px;color:#333}
.slide-arrow{top:261px}

.samples-title{left:0;top:554px;width:1080px;text-align:center;color:var(--heading);font-weight:700;font-size:21px}
.sample-thumb{width:97px;height:84px;border:3px solid #fff;box-shadow:0 0 0 1px #ddd}
.sample-label{font-size:13px;line-height:18px;color:#444}

.perks-band{left:2px;top:840px;width:1078px;height:133px;background:var(--band);border-top:1px solid #e2e2e2}
.perk-label{font-size:13px;line-height:18px;color:#555}

.signup{left:0;top:973px;width:1080px;height:185px;background:var(--sky)}
.signup-title{left:155px;top:1001px;color:var(--white);font-size:14px}
.signup-copy{left:155px;top:1030px;width:255px;color:var(--white);font-size:9px;line-height:18.5px}
.no-card{left:155px;top:1095px;width:237px;height:28px;border:1px solid var(--white);color:var(--white);font-size:9px;display:flex;align-items:center;justify-content:center}
.email-field{left:440px;top:1049px;width:237px;height:28px;background:var(--white);color:#999;font-size:8px;padding-left:14px;display:flex;align-items:center}
.access-btn{left:713px;top:1009px;width:213px;height:38px;background:var(--access);color:var(--white);font-size:11.5px;display:flex;align-items:center;justify-content:center}
.or{left:713px;top:1057px;width:213px;text-align:center;color:var(--white);font-size:11px}
.social-btn{left:713px;top:1079px;width:213px;height:38px;background:var(--social);color:var(--white);font-size:11.5px;display:flex;align-items:center}
.social-btn .mark{width:43px;height:38px;background:var(--social-dark);display:flex;align-items:center;justify-content:center}
.social-btn .mark span{width:10px;height:10px;background:var(--white)}
.social-btn .txt{padding-left:12px}

.footer{left:0;top:1158px;width:1080px;height:42px;background:var(--sky-deep)}
.footer-links{left:157px;top:1174px;color:var(--white);font-size:8px;display:flex;gap:12px}
.copyright{left:700px;top:1174px;width:226px;text-align:right;color:var(--white);font-size:8px}
</style>
</head>
<body>

<header class="abs topbar"></header>
<div class="abs brand"><span class="brand-dot"></span>Dunmoral</div>
<div class="abs member-login">MEMBER LOGIN</div>

<section class="abs hero"></section>
<div class="abs hero-photo" role="img" aria-label="Smiling young man wearing headphones, looking at his phone"></div>
<div class="abs hero-fade"></div>
<h1 class="abs headline">UNLIMITED LISTENING.</h1>
<h2 class="abs subline">WHEREVER YOU ARE.</h2>
<p class="abs price">Only $9.99 per month</p>
<div class="abs cta-trial">Start Your Free Trial</div>
<p class="abs trial-note">* Credit Card Not Required</p>
<svg class="abs slide-arrow" style="left:56px" width="42" height="42" viewBox="0 0 42 42"><circle cx="21" cy="21" r="19.5" fill="rgba(255,255,255,.4)" stroke="#cfe4f0" stroke-width="2"/><path d="M27 12 L13 21 L27 30 L23 21 Z" fill="#cfe4f0"/></svg>
<svg class="abs slide-arrow" style="left:981px" width="42" height="42" viewBox="0 0 42 42"><circle cx="21" cy="21" r="19.5" fill="rgba(255,255,255,.15)" stroke="#cfe4f0" stroke-width="2"/><path d="M15 12 L29 21 L15 30 L19 21 Z" fill="#cfe4f0"/></svg>

<h3 class="abs samples-title">A SAMPLE OF WHAT YOU CAN LISTEN TO ON DUNMORAL</h3>

<div class="abs sample-thumb" style="left:155px;top:610px;background:linear-gradient(#3a4d5a,#1c2329)" role="img" aria-label="Noir audiobook cover"></div>
<p class="abs sample-label" style="left:268px;top:640px">Audiobooks</p>
<div class="abs sample-thumb" style="left:350px;top:610px;background:linear-gradient(#6d6d6d,#2a2a2a)" role="img" aria-label="Stand-up comedy album cover"></div>
<p class="abs sample-label" style="left:463px;top:636px">Stand-Up<br>Comedy</p>
<div class="abs sample-thumb" style="left:550px;top:610px;background:linear-gradient(#2d8fd6,#0f5fa8)" role="img" aria-label="French language course cover"></div>
<p class="abs sample-label" style="left:663px;top:637px">Language<br>Learning</p>
<div class="abs sample-thumb" style="left:745px;top:610px;background:linear-gradient(#c9b8a4,#8eb169)" role="img" aria-label="Biography audiobook cover"></div>
<p class="abs sample-label" style="left:858px;top:633px">Biographies<br>&amp; Memoirs</p>

<div class="abs sample-thumb" style="left:155px;top:717px;background:linear-gradient(#c46fae,#6b3a8f)" role="img" aria-label="Total relaxation meditation cover"></div>
<p class="abs sample-label" style="left:265px;top:742px">Guided<br>Meditations</p>
<div class="abs sample-thumb" style="left:350px;top:717px;background:linear-gradient(#5a3b22,#1e1a18)" role="img" aria-label="Business training program cover"></div>
<p class="abs sample-label" style="left:463px;top:742px">Business<br>Training</p>
<div class="abs sample-thumb" style="left:550px;top:717px;background:linear-gradient(#b58c6a,#7a4a5a)" role="img" aria-label="Celebrity interview cover"></div>
<p class="abs sample-label" style="left:663px;top:743px">Celebrity<br>Interviews</p>
<div class="abs sample-thumb" style="left:745px;top:717px;background:linear-gradient(#2aa3dc,#1a6fa5)" role="img" aria-label="Elliptical fitness coaching cover"></div>
<p class="abs sample-label" style="left:858px;top:738px">Fitness<br>Programs</p>

<section class="abs perks-band"></section>
<div class="abs sample-thumb" style="left:155px;top:864px;background:linear-gradient(135deg,#d9c2b0,#6b5a52)" role="img" aria-label="Hand holding a smartphone"></div>
<p class="abs perk-label" style="left:265px;top:887px">Listen on your Zarno,<br>Tavo or Rovix device.</p>
<div class="abs sample-thumb" style="left:418px;top:864px;background:linear-gradient(135deg,#eef1f3,#a9b9a3)" role="img" aria-label="Watering can over a dollar-shaped plant"></div>
<p class="abs perk-label" style="left:527px;top:887px">All you can enjoy for one<br>low monthly price.</p>
<div class="abs sample-thumb" style="left:691px;top:864px;background:linear-gradient(135deg,#f4f4f4,#222)" role="img" aria-label="Close-up of a clock face"></div>
<p class="abs perk-label" style="left:800px;top:887px">No obligation. Cancel<br>any time.</p>

<section class="abs signup"></section>
<h4 class="abs signup-title">START YOUR FREE TRIAL</h4>
<p class="abs signup-copy">You will get instant &amp; unlimited access to all the material on Dunmoral for 14 days. There is no obligation &amp; you can cancel at any time.</p>
<div class="abs no-card">CREDIT CARD NOT REQUIRED FOR FREE TRIAL</div>
<div class="abs email-field">YOUR EMAIL ADDRESS :</div>
<div class="abs access-btn">GET INSTANT ACCESS</div>
<p class="abs or">OR</p>
<div class="abs social-btn"><span class="mark"><span></span></span><span class="txt">SIGN UP USING CHATTERLY</span></div>

<footer class="abs footer"></footer>
<nav class="abs footer-links"><span>About</span><span>|</span><span>Help</span><span>|</span><span>Contact Us</span><span>|</span><span>Member Login</span><span>|</span><span>Privacy Policy</span><span>|</span><span>Terms of Service</span></nav>
<p class="abs copyright">©2014 Dunmoral LLC - All Rights Reserved</p>

</body>
</html>
```